Business Card Design Project

Business Card design based on logo.
Updates

I need business card, letterhead, envelope, and if possible, Powerpoint slide template.

On front of business card: Just logo- and  my name and title:  Harriet Lindqvist, Principal

On reverse-logo and the rest of the contact info:

4871 Quarry Lane
Davis, CA 95618
650-318-2764
hl@brackenstudyworks.example

On letterhead-Just logo at top, at bottom  the rest-very small along the bottom

On PPT slide-just the logo.

I also want to try a few other colors-I like lime/dark grey (not black) but would like to try Sienna, maybe also indigo or bright blue-green.

I forgot to add-

On the business card-switch to vertical on reverse side and put:

Reverse side-switch to vertical and list:

Harriet Lindqvist
Principal
Bracken Study Works, LLC

650-318-2764

4871 Quarry Lane
Davis, CA 95618

Harriet Lindqvist
Principal

650-318-2764

4871 Quarry Lane
Davis, CA 95618

I have another project at the same time-for Stationery. Feel free to submit to that one also.

That one includes letterhead, envelope, PPT slide, folder cover sheet-HL

Industry/Entity Type

Business

Requirements
Must have
• Must use logo-preferably lime green version-with gray, not black or just 2-tone -logo on colored background.

```html
<!DOCTYPE html>
<html lang="en">
<head>
<meta charset="utf-8">
<title>Bracken Study Works – Business Cards</title>
<link rel="stylesheet" href="https://fonts.googleapis.com/css2?family=Playfair+Display:wght@400&family=Open+Sans:wght@400;700&display=swap">
<style>
  :root {
    --stage: #1b1b1b;
    --lime: #9bbb2f;
    --graphite: #454547;
    --ink: #111111;
    --paper: #ffffff;
    --serif: "Playfair Display", Georgia, serif;
    --sans: "Open Sans", Arial, sans-serif;
  }
  * { box-sizing: border-box; margin: 0; padding: 0; }
  html, body { width: 1200px; height: 722px; overflow: hidden; }
  body { background: var(--stage); position: relative; font-family: var(--sans); }

  .card {
    position: absolute;
    width: 525px;
    height: 300px;
    border-radius: 14px;
    overflow: hidden;
    text-align: center;
  }
  .card--front    { left: 58px;  top: 47px;  background: var(--paper); }
  .card--white    { left: 612px; top: 47px;  background: var(--paper); }
  .card--lime     { left: 62px;  top: 376px; background: var(--lime); }
  .card--graphite { left: 612px; top: 376px; background: var(--graphite); }

  .brand { position: absolute; left: 0; right: 0; }
  .brand__mark { display: block; margin: 0 auto 12px; width: 16px; height: 16px; }
  .brand__name {
    font-family: var(--serif);
    font-weight: 400;
    letter-spacing: 3px;
    line-height: 1.1;
    text-transform: uppercase;
  }

  .card--front .brand { top: 40px; }
  .card--front .brand__mark { background: var(--lime); }
  .card--front .brand__name { color: var(--graphite); font-size: 24px; }

  .holder {
    position: absolute; top: 158px; left: 0; right: 0;
    color: var(--lime); font-weight: 700; font-size: 15px;
  }
  .holder__title { font-weight: 400; font-size: 12px; }

  .wave { position: absolute; left: 0; top: 0; width: 525px; height: 300px; }
  .wave__band { fill: var(--lime); }
  .wave__base { fill: var(--graphite); }

  .contact {
    position: absolute; left: 0; right: 0; top: 228px;
    color: var(--paper); font-size: 13px; line-height: 1;
  }
  .contact__line { margin-bottom: 10px; }
  .contact__item { display: inline-flex; align-items: center; gap: 5px; margin: 0 7px; }
  .contact__icon { width: 11px; height: 11px; fill: var(--paper); }

  .card--white .brand { top: 72px; }
  .card--white .brand__mark { background: var(--lime); }
  .card--white .brand__name { color: var(--graphite); font-size: 30px; }

  .card--lime .brand { top: 76px; }
  .card--lime .brand__mark { background: var(--ink); }
  .card--lime .brand__name { color: var(--ink); font-size: 30px; }

  .card--graphite .brand { top: 100px; }
  .card--graphite .brand__name { color: var(--lime); font-size: 38px; letter-spacing: 4px; }

  .site {
    position: absolute; left: 0; right: 0;
    font-size: 12px; letter-spacing: 2.4px;
  }
  .card--white .site { top: 221px; color: var(--ink); }
  .card--lime .site { top: 244px; color: var(--paper); }
  .card--graphite .site { top: 244px; color: var(--paper); }
  .site__domain { color: var(--lime); }
  .card--lime .site__domain { color: var(--paper); }
</style>
</head>
<body>

  <section class="card card--front" aria-label="Card front">
    <div class="brand">
      <span class="brand__mark"></span>
      <p class="brand__name">Bracken<br>Study Works</p>
    </div>
    <p class="holder">HARRIET LINDQVIST, <span class="holder__title">Principal</span></p>
    <svg class="wave" viewBox="0 0 525 300" aria-hidden="true">
      <path class="wave__band" d="M0,172 C120,196 260,192 525,210 L525,218 C300,200 150,204 0,194 Z"/>
      <path class="wave__base" d="M0,202 C150,208 300,198 525,222 L525,300 L0,300 Z"/>
    </svg>
    <div class="contact">
      <p class="contact__line">4871 Quarry Lane, Davis, CA 95618</p>
      <p class="contact__line">
        <span class="contact__item">
          <svg class="contact__icon" viewBox="0 0 12 12"><path d="M2.5 1l2 2.2-1.2 1.4a7 7 0 0 0 4.1 4.1l1.4-1.2L11 9.5 9.6 11C5 10.6 1.4 7 1 2.4z"/></svg>650-318-2764
        </span>
        <span class="contact__item">
          <svg class="contact__icon" viewBox="0 0 12 12"><path d="M1 3h10v7H1z M1 3l5 4 5-4" stroke="#454547" stroke-width="1"/></svg>hl@brackenstudyworks.example
        </span>
      </p>
      <p class="contact__line">www.brackenstudyworks.example</p>
    </div>
  </section>

  <section class="card card--white" aria-label="Card back, white">
    <div class="brand">
      <span class="brand__mark"></span>
      <p class="brand__name">Bracken<br>Study Works</p>
    </div>
    <p class="site">www.<span class="site__domain">brackenstudyworks</span>.example</p>
  </section>

  <section class="card card--lime" aria-label="Card back, lime">
    <div class="brand">
      <span class="brand__mark"></span>
      <p class="brand__name">Bracken<br>Study Works</p>
    </div>
    <p class="site">www.<span class="site__domain">brackenstudyworks</span>.example</p>
  </section>

  <section class="card card--graphite" aria-label="Card back, graphite">
    <div class="brand">
      <p class="brand__name">Bracken<br>Study Works</p>
    </div>
    <p class="site">www.<span class="site__domain">brackenstudyworks</span>.example</p>
  </section>

</body>
</html>
```